Our companies name is The Gilded Ladle and we specialize in craft cupcakes, what I mean by that is that we bake our cupcakes with craft beer and other alcoholic drinks. We are trying to focus on being elegant but at the same time unpretentious. Since we are incorporating beer in our cupcakes we want the business card to have our logo in the front and our information in the back.

Once we select the best design we will provide the contact information to be added. Thank you.

Industry/Entity Type

Business

Font styles to use
Decorative
Script

Requirements
Must have
• Round corners
Should not have
• Square corners

```html
<!DOCTYPE html>
<html lang="en">
<head>
<meta charset="utf-8">
<title>The Gilded Ladle — Business Card</title>
<link rel="stylesheet" href="https://fonts.googleapis.com/css2?family=Alfa+Slab+One&family=Arimo:wght@400;700&display=swap">
<style>
  :root {
    --bg: #3a3a3e;
    --card: #f7fbfb;
    --ink: #111111;
    --band: #0b0b0b;
    --accent: #e0201f;
    --muted: #555;
  }
  * { box-sizing: border-box; margin: 0; padding: 0; }
  html, body { width: 1200px; height: 960px; overflow: hidden; }
  body {
    background: var(--bg);
    font-family: "Arimo", Arial, sans-serif;
    display: flex; flex-direction: column; align-items: center; justify-content: center;
    gap: 60px;
  }
  .card {
    position: relative;
    width: 640px; height: 366px;
    background: var(--card);
    border-radius: 22px;
    overflow: hidden;
    box-shadow: 0 14px 30px rgba(0,0,0,.45);
  }
  .brand {
    position: absolute;
    display: flex; align-items: center; gap: 14px;
    font-family: "Alfa Slab One", Georgia, serif;
    color: var(--ink);
    white-space: nowrap;
  }
  .brand-dot { width: 22px; height: 22px; border-radius: 50%; background: var(--accent); flex: none; }
  .front .brand { left: 50%; top: 44%; transform: translate(-50%, -50%); font-size: 40px; }
  .band-svg { position: absolute; left: 0; width: 100%; }
  .front .band-svg { bottom: 0; height: 70px; }

  .back .logo-side { position: absolute; left: 0; top: 0; width: 44%; height: 100%; }
  .back .brand { left: 50%; top: 50%; transform: translate(-50%, -50%); font-size: 24px; gap: 10px; }
  .back .brand-dot { width: 16px; height: 16px; }
  .back .divider {
    position: absolute; left: 44%; top: 0; width: 2px; height: 100%;
    background: linear-gradient(#bbb, #ddd);
    box-shadow: -4px 0 8px rgba(0,0,0,.12);
  }
  .back .band-top { top: 0; height: 56px; }
  .back .band-bottom { bottom: 0; height: 60px; }
  .info { position: absolute; left: calc(44% + 34px); top: 74px; right: 24px; color: var(--ink); }
  .name {
    font-family: "Alfa Slab One", Georgia, serif;
    color: var(--accent); font-size: 25px; letter-spacing: .5px; line-height: 1;
  }
  .role { font-size: 14px; margin-top: 3px; }
  .contacts { list-style: none; margin-top: 26px; font-size: 15px; line-height: 22px; }
  .contacts li { display: flex; align-items: center; gap: 10px; }
  .contacts svg { width: 12px; height: 12px; flex: none; }
  .address { margin-top: 28px; font-size: 17px; line-height: 21px; }
</style>
</head>
<body>
  <section class="card front" aria-label="Card front">
    <div class="brand"><span class="brand-dot"></span>The Gilded Ladle</div>
    <svg class="band-svg" viewBox="0 0 640 70" preserveAspectRatio="none" aria-hidden="true">
      <polygon points="0,30 280,30 310,8 640,8 640,70 0,70" fill="var(--accent)"/>
      <polygon points="0,36 284,36 314,14 640,14 640,70 0,70" fill="var(--band)"/>
    </svg>
  </section>

  <section class="card back" aria-label="Card back">
    <div class="logo-side">
      <div class="brand"><span class="brand-dot"></span>The Gilded Ladle</div>
    </div>
    <div class="divider"></div>
    <svg class="band-svg band-top" viewBox="0 0 640 56" preserveAspectRatio="none" aria-hidden="true">
      <polygon points="282,0 640,0 640,10 560,10 520,40 282,40" fill="var(--band)"/>
      <polygon points="520,40 560,10 640,10 640,14 562,14 524,42" fill="var(--accent)"/>
    </svg>
    <svg class="band-svg band-bottom" viewBox="0 0 640 60" preserveAspectRatio="none" aria-hidden="true">
      <polygon points="282,26 560,26 600,4 640,4 640,60 282,60" fill="var(--accent)"/>
      <polygon points="282,31 562,31 602,9 640,9 640,60 282,60" fill="var(--band)"/>
    </svg>
    <div class="info">
      <p class="name">EMPLOYEE NAME</p>
      <p class="role">Managing Director</p>
      <ul class="contacts">
        <li><svg viewBox="0 0 12 12"><path d="M2 1h3l1 3-2 1a7 7 0 0 0 3 3l1-2 3 1v3c-6 0-10-4-10-9z" fill="var(--accent)"/></svg>(xxx) xxx-xxxx</li>
        <li><svg viewBox="0 0 12 12"><rect x="1" y="3" width="10" height="7" rx="1" fill="var(--accent)"/><rect x="3" y="1" width="6" height="3" fill="var(--accent)"/></svg>xxx-xxx-xxxx</li>
        <li><svg viewBox="0 0 12 12"><circle cx="6" cy="6" r="5" fill="var(--accent)"/><path d="M1 6h10M6 1v10" stroke="#fff" stroke-width="1"/></svg>www.yourwebsit.com</li>
        <li><svg viewBox="0 0 12 12"><rect x="1" y="2.5" width="10" height="7" fill="var(--accent)"/><path d="M1 2.5l5 4 5-4" stroke="#fff" fill="none" stroke-width="1"/></svg>Info@youremail.com</li>
      </ul>
      <p class="address">Your Address Inc 2nd Lane Ave Brookvale,<br>NJ 00000</p>
    </div>
  </section>
</body>
</html>
```